Psychiatric Office Needs a Website- 1st Time Ever!

Been in practice since 2003 with no website, but finally ready to dive in. We are Maplecrest Behavioral Healthcare, a mental health outpatient practice based in Fayetteville, Georgia that sees diverse individuals and families from childhood to advanced age for a variety of conditions. We've grown by word of mouth and referral but would now like to have a digital footprint. Be the pioneer of our website and we will be sure to share. We would like to see designs that are modern, animated, fairly colorful, easy to read, and caters to all ages. Also, we would like the design to take the whole page (not be centered) and can be viewed well on phone/tablet. Please see our outline for more information. Our motto/slogan is: Maplecrest Behavioral Healthcare- A step forward in your wellness journey, so the design should try to reflect that.
Updates

Project Deadline Extended
Reason: site in progress

Target Market(s)

Children through elderly

Industry/Entity Type

Medical

Logo Text

Stepping forward in your wellness journey

Number of Pages Required

1 page

Colors

Designer to choose colors to be used in the design.

Requirements
Must have
• Animation or moving pictures.
• Color.
• Concise.
• User friendly
• Diversity in the stock photos

```html
<!DOCTYPE html>
<html lang="en">
<head>
<meta charset="utf-8">
<title>Maplecrest Behavioral Healthcare</title>
<link href="https://fonts.googleapis.com/css2?family=PT+Sans:ital,wght@0,400;0,700;1,400&family=Signika:wght@400;600&display=swap" rel="stylesheet">
<style>
:root{
  --green:#0da54a;
  --green-dark:#06893a;
  --green-light:#12b857;
  --ink:#333;
  --muted:#666;
  --topbar:#3a3a3a;
  --dark:#2b2b2b;
  --white:#fff;
  --line:#d9d9d9;
}
*{margin:0;padding:0;box-sizing:border-box}
html,body{width:1200px;height:3455px;overflow:hidden}
body{font-family:"PT Sans",Arial,sans-serif;color:var(--ink);background:var(--white);position:relative}
.abs{position:absolute}
h2,h3,.heading{font-family:"Signika","PT Sans",sans-serif;font-weight:400}

/* top bar + nav */
.topbar{left:0;top:0;width:1200px;height:46px;background:var(--topbar);color:#eee;font-size:14px}
.topbar span{position:absolute;top:14px}
.navbar{left:0;top:46px;width:1200px;height:74px;background:var(--white);box-shadow:0 2px 4px rgba(0,0,0,.1)}
.nav-home{left:358px;top:36px;width:102px;height:84px;background:var(--green);color:#fff;font-size:17px;text-align:center;padding-top:38px}
.nav-link{top:76px;font-size:17px;color:#444}
.brand{left:80px;top:8px;width:112px;height:112px;border-radius:50%;background:var(--green);border:5px solid #fff;box-shadow:0 0 0 2px var(--green);color:#fff;font-size:13px;font-weight:700;text-align:center;display:flex;align-items:center;justify-content:center;padding:10px;line-height:1.25}

/* hero */
.hero{left:0;top:120px;width:1200px;height:571px;background:linear-gradient(160deg,#b7a99a 0%,#7d746c 40%,#4b4642 100%)}
.hero-box{left:210px;top:282px;width:780px;height:196px;background:rgba(40,40,40,.55);text-align:center;color:#fff}
.hero-box h1{font-family:"Signika",sans-serif;font-weight:400;font-size:50px;margin-top:22px}
.hero-box p{font-style:italic;font-size:20px;margin-top:2px}
.btn-green{display:inline-block;background:var(--green);color:#fff;font-size:20px;padding:14px 34px;margin-top:16px}

/* vision / mission */
.vision{left:0;top:691px;width:600px;height:368px;background:var(--green);color:#fff}
.mission{left:600px;top:691px;width:600px;height:368px;background:#fff}
.vm-title{font-size:36px;font-family:"Signika",sans-serif;display:flex;align-items:center;gap:12px}
.vm-text{font-size:15.5px;line-height:1.7}
.seal{left:450px;top:694px;width:300px;height:300px;border-radius:50%;background:#fff;display:flex;align-items:center;justify-content:center}
.seal-inner{width:270px;height:270px;border-radius:50%;background:var(--green);color:#fff;display:flex;align-items:center;justify-content:center;text-align:center;font-size:22px;font-weight:700;padding:30px;line-height:1.3}

/* services */
.services{left:0;top:1059px;width:1200px;height:834px;background:linear-gradient(180deg,#3c3c3c,#2a2a2a 60%,#333)}
.section-title{font-family:"Signika",sans-serif;font-size:36px;text-align:center;width:1200px;left:0}
.section-title::after{content:"";display:block;width:150px;height:2px;background:currentColor;margin:10px auto 0;opacity:.8}
.svc{color:#fff;font-size:14.5px;line-height:1.45;width:230px}
.svc b{display:block;color:var(--green-light);font-weight:400;font-size:16px;margin-bottom:2px;white-space:nowrap}
.svc u{font-weight:700;white-space:nowrap}

/* conditions */
.conditions{left:0;top:1893px;width:1200px;height:548px;background:linear-gradient(180deg,var(--green) 0%,var(--green-dark) 100%);color:#fff}
.cond-card{top:2043px;width:253px;text-align:center;color:#fff}
.cond-photo{width:253px;height:168px;background:linear-gradient(135deg,#8a7466,#c9b2a0 55%,#5e4d44);box-shadow:0 4px 10px rgba(0,0,0,.3)}
.cond-card h3{font-size:21px;margin-top:20px;line-height:1.15}
.cond-card p{font-size:13.5px;line-height:1.5;margin-top:14px}
.arrow-btn{top:2107px;width:30px;height:30px;background:#fff;border:1px solid #ccc;display:flex;align-items:center;justify-content:center}
.dot{top:2412px;width:12px;height:12px;border:1px solid #fff}

/* faq + news */
.faq-title,.news-title{font-family:"Signika",sans-serif;font-size:36px;color:var(--green)}
.faq-item{left:80px;width:518px;height:44px;border:1px solid var(--line);color:var(--green-dark);font-size:19px;display:flex;align-items:center;gap:12px;padding-left:14px;background:#fff}
.faq-body{left:80px;top:2596px;width:518px;height:96px;border:1px solid var(--line);border-top:0;font-size:12.5px;line-height:1.55;color:#555;padding:8px 14px}
.news-photo{width:116px;background:linear-gradient(135deg,#6f7f95,#c7b4a4)}
.news h4{color:var(--green);font-weight:400;font-size:19px}
.news .date{font-size:12px;color:#777;margin-top:6px}
.news p{font-size:14px;color:#555;line-height:1.45;margin-top:4px}
.news .more{color:var(--green);font-size:13px;margin-top:10px;font-weight:700}

/* band */
.band{left:0;top:2874px;width:1200px;height:104px;background:var(--green);color:#fff;font-size:15.5px;line-height:1.6}
.btn-white{left:910px;top:2898px;width:212px;height:56px;background:#fff;color:#333;font-size:19px;display:flex;align-items:center;justify-content:center}

/* footer */
.footer{left:0;top:2978px;width:1200px;height:407px;background:linear-gradient(180deg,rgba(40,28,24,.93),rgba(30,22,20,.96)),linear-gradient(90deg,#6a4a3c,#3a2a24)}
.foot-h{color:#fff;font-size:20px;top:3030px;letter-spacing:.5px}
.field{left:80px;width:448px;height:42px;background:#fff;font-size:14px;color:#555;padding:12px 10px}
.submit{left:80px;top:3325px;width:184px;height:53px;background:var(--green);color:#fff;font-size:19px;display:flex;align-items:center;justify-content:center}
.foot-list{left:570px;top:3078px;color:#fff;font-size:15px;line-height:29px;list-style:none}
.foot-list li::before{content:"";display:inline-block;width:7px;height:7px;border-radius:50%;background:var(--green);margin-right:14px;vertical-align:middle}
.find{color:#fff;font-size:14.5px;line-height:1.5}
.social{top:3308px;width:46px;height:46px;border-radius:50%;background:var(--green)}
.copyright{left:0;top:3385px;width:1200px;height:70px;background:#241a17;color:#fff;font-size:15px;text-align:center;padding-top:24px;letter-spacing:.5px;border-top:1px solid #555}
</style>
</head>
<body>

<!-- header -->
<div class="abs topbar">
  <span style="left:505px">
    <svg width="16" height="16" viewBox="0 0 16 16" style="vertical-align:-3px"><circle cx="8" cy="8" r="6.5" fill="none" stroke="var(--green-light)" stroke-width="1.5"/><path d="M8 4v4l3 2" stroke="var(--green-light)" stroke-width="1.5" fill="none"/></svg>
    &nbsp;Monday - Friday : 10.00 A.M to 8.00 P.M</span>
  <span style="left:820px">
    <svg width="16" height="16" viewBox="0 0 16 16" style="vertical-align:-3px"><circle cx="8" cy="8" r="6.5" fill="none" stroke="var(--green-light)" stroke-width="1.5"/><path d="M5 5l2 0 1 2-1 1 2 2 1-1 2 1v2c-4 0-7-3-7-7z" fill="var(--green-light)"/></svg>
    &nbsp;+1-555-010-2040</span>
  <span style="left:980px">LOGIN</span>
  <span style="left:1038px">
    <svg width="14" height="16" viewBox="0 0 14 16" style="vertical-align:-3px"><circle cx="7" cy="4.5" r="3.5" fill="var(--green-light)"/><path d="M0 16c0-5 3-7 7-7s7 2 7 7z" fill="var(--green-light)"/></svg>
    &nbsp;Patient</span>
</div>
<div class="abs navbar"></div>
<div class="abs nav-home">Home</div>
<span class="abs nav-link" style="left:505px">About Us</span>
<span class="abs nav-link" style="left:605px">Services</span>
<span class="abs nav-link" style="left:700px">Conditions We Treat</span>
<span class="abs nav-link" style="left:888px">New Patients</span>
<span class="abs nav-link" style="left:1020px">Contact Us</span>
<div class="abs brand">Maplecrest Behavioral Healthcare</div>

<!-- hero -->
<div class="abs hero" role="img" aria-label="Photo of a cheerful group of colleagues celebrating around an office table"></div>
<div class="abs hero-box">
  <h1>Maplecrest Behavioral Healthcare</h1>
  <p>A step forward in your wellness journey</p>
  <span class="btn-green">CONTACT US</span>
</div>

<!-- vision / mission -->
<section class="abs vision">
  <div class="abs vm-title" style="left:78px;top:44px">
    <svg width="30" height="34" viewBox="0 0 30 34"><path d="M4 30l10-14M14 16l10-12M24 4l3 3-12 12" stroke="#fff" stroke-width="3" fill="none"/><path d="M14 16l-6 16M14 16l6 16" stroke="#fff" stroke-width="2.5"/></svg>
    VISION
  </div>
  <div class="abs" style="left:78px;top:98px;width:170px;height:1px;background:#fff"></div>
  <p class="abs vm-text" style="left:78px;top:120px;width:345px">Lorem Ipsum is simply dummy text of the printing and typesetting industry. Lorem Ipsum has been the industry's standard dummy text ever since the 1500s, when an unknown printer took a galley of type and scrambled it to make a type specimen book. It has survived not only five centuries, but also the leap into electronic typesetting, remaining essentially unchanged.</p>
</section>
<section class="abs mission">
  <div class="abs vm-title" style="left:170px;top:44px;color:var(--green)">
    <svg width="34" height="34" viewBox="0 0 34 34"><circle cx="15" cy="19" r="12" fill="none" stroke="var(--green)" stroke-width="3"/><circle cx="15" cy="19" r="5" fill="none" stroke="var(--green)" stroke-width="3"/><path d="M15 19L31 3M25 3h6v6" stroke="var(--green)" stroke-width="3" fill="none"/></svg>
    MISSION
  </div>
  <div class="abs" style="left:170px;top:98px;width:180px;height:1px;background:var(--green)"></div>
  <p class="abs vm-text" style="left:172px;top:120px;width:345px;color:#555">Lorem Ipsum is simply dummy text of the printing and typesetting industry. Lorem Ipsum has been the industry's standard dummy text ever since the 1500s, when an unknown printer took a galley of type and scrambled it to make a type specimen book. It has survived not only five centuries, but also the leap into electronic typesetting, remaining essentially unchanged.</p>
</section>
<div class="abs seal"><div class="seal-inner">Maplecrest Behavioral Healthcare</div></div>

<!-- services -->
<section class="abs services" role="img" aria-label="Dimmed photo of a counselling office as section background"></section>
<h2 class="abs section-title" style="top:1103px;color:#fff">SERVICES</h2>
<svg class="abs" style="left:0;top:1059px" width="1200" height="834" viewBox="0 1059 1200 834">
  <g stroke="var(--green)" stroke-width="2">
    <line x1="600" y1="1440" x2="504" y2="1264"/><line x1="600" y1="1440" x2="686" y2="1251"/>
    <line x1="600" y1="1440" x2="396" y2="1375"/><line x1="600" y1="1440" x2="799" y2="1396"/>
    <line x1="600" y1="1440" x2="442" y2="1589"/><line x1="600" y1="1440" x2="765" y2="1584"/>
    <line x1="600" y1="1440" x2="608" y2="1663"/>
  </g>
  <circle cx="600" cy="1440" r="108" fill="#fff" stroke="#ddd" stroke-width="6"/>
  <circle cx="600" cy="1440" r="30" fill="var(--green)"/>
  <g fill="var(--green)">
    <circle cx="520" cy="1422" r="6"/><circle cx="680" cy="1422" r="6"/>
    <circle cx="560" cy="1366" r="6"/><circle cx="640" cy="1366" r="6"/>
    <circle cx="530" cy="1487" r="6"/><circle cx="670" cy="1487" r="6"/>
    <circle cx="600" cy="1530" r="6"/>
  </g>
  <g fill="#9a8a80" stroke="#fff" stroke-width="4">
    <circle cx="504" cy="1264" r="62"/><circle cx="686" cy="1251" r="62"/>
    <circle cx="396" cy="1375" r="62"/><circle cx="799" cy="1396" r="62"/>
    <circle cx="442" cy="1589" r="62"/><circle cx="765" cy="1584" r="62"/>
    <circle cx="608" cy="1663" r="62"/>
  </g>
  <g fill="none" stroke="var(--green)" stroke-width="5">
    <circle cx="504" cy="1264" r="67"/><circle cx="686" cy="1251" r="67"/>
    <circle cx="396" cy="1375" r="67"/><circle cx="799" cy="1396" r="67"/>
    <circle cx="442" cy="1589" r="67"/><circle cx="765" cy="1584" r="67"/>
    <circle cx="608" cy="1663" r="67"/>
  </g>
</svg>
<div class="abs svc" style="left:138px;top:1217px"><b>Diagnostic evaluation and treatment</b>Lorem Ipsum is simply dummy text of the printing and text typesetting industry.<u>READ MORE</u></div>
<div class="abs svc" style="left:771px;top:1199px"><b>Disability and work-related reports</b>Lorem Ipsum is simply dummy text of the printing and text typesetting industry.<u>READ MORE</u></div>
<div class="abs svc" style="left:81px;top:1383px"><b>Psychopharmacology</b>Lorem Ipsum is simply dummy text of the printing and text typesetting industry.<u>READ MORE</u></div>
<div class="abs svc" style="left:887px;top:1358px"><b>Early childhood Assessments</b>Lorem Ipsum is simply dummy text of the printing and text typesetting industry.<u>READ MORE</u></div>
<div class="abs svc" style="left:101px;top:1572px"><b>Bariatric pre-surgical consultation</b>Lorem Ipsum is simply dummy text of the printing and text typesetting industry.<u>READ MORE</u></div>
<div class="abs svc" style="left:864px;top:1544px"><b>Substance abuse assessments</b>Lorem Ipsum is simply dummy text of the printing and text typesetting industry.<u>READ MORE</u></div>
<div class="abs svc" style="left:502px;top:1749px;width:220px"><b>Developmental disabilities</b>Lorem Ipsum is simply dummy text of the printing and text typesetting industry.<u>READ MORE</u></div>

<!-- conditions -->
<section class="abs conditions"></section>
<h2 class="abs section-title" style="top:1950px;color:#fff">CONDITIOND WE TREAT</h2>
<div class="abs cond-card" style="left:78px">
  <div class="cond-photo" role="img" aria-label="Photo of a stressed woman holding her head"></div>
  <h3>Mood Disorders</h3>
  <p>Lorem Ipsum is simply dummy text of the printing and typesetting industry. Lorem Ipsum has been the industry's standard dummy text ever since.</p>
</div>
<div class="abs cond-card" style="left:343px">
  <div class="cond-photo" role="img" aria-label="Photo of a counsellor talking with a patient"></div>
  <h3>Anxiety Disorders</h3>
  <p>Lorem Ipsum is simply dummy text of the printing and typesetting industry. Lorem Ipsum has been the industry's standard dummy text ever since.</p>
</div>
<div class="abs cond-card" style="left:608px">
  <div class="cond-photo" role="img" aria-label="Photo of a therapy session in a bright office"></div>
  <h3>Psychotic Disorders</h3>
  <p>Lorem Ipsum is simply dummy text of the printing and typesetting industry. Lorem Ipsum has been the industry's standard dummy text ever since.</p>
</div>
<div class="abs cond-card" style="left:873px">
  <div class="cond-photo" role="img" aria-label="Photo of a mother hugging her child"></div>
  <h3>Common Disorders<br>of Childhood</h3>
  <p style="margin-top:8px">Lorem Ipsum is simply dummy text of the printing and typesetting industry. Lorem Ipsum has been the industry's standard dummy text ever since.</p>
</div>
<div class="abs arrow-btn" style="left:32px"><svg width="10" height="14" viewBox="0 0 10 14"><path d="M8 1L2 7l6 6" stroke="#555" stroke-width="2" fill="none"/></svg></div>
<div class="abs arrow-btn" style="left:1138px"><svg width="10" height="14" viewBox="0 0 10 14"><path d="M2 1l6 6-6 6" stroke="#555" stroke-width="2" fill="none"/></svg></div>
<div class="abs dot" style="left:572px"></div>
<div class="abs dot" style="left:590px;background:#fff"></div>
<div class="abs dot" style="left:608px"></div>

<!-- faq -->
<div class="abs" style="left:610px;top:2441px;width:8px;height:433px;background:#eee"></div>
<h2 class="abs faq-title" style="left:80px;top:2490px">FAQ</h2>
<div class="abs" style="left:80px;top:2538px;width:518px;height:1px;background:var(--line)"></div>
<div class="abs faq-item" style="top:2552px"><span style="font-size:26px;font-weight:700">&minus;</span>What do I need to bring with me to my first visit?</div>
<div class="abs faq-body">Lorem Ipsum is simply dummy text of the printing and typesetting industry. Lorem Ipsum has been the industry's standard dummy text ever since the 1500s.It has survived not only five centuries, but also the leap into electronic typesetting, remaining essentially unchanged.</div>
<div class="abs faq-item" style="top:2684px"><span style="font-size:26px;font-weight:700">+</span>How long do I have to wait to be seen?</div>
<div class="abs faq-item" style="top:2727px"><span style="font-size:26px;font-weight:700">+</span>Why is my child not doing well in school?</div>
<div class="abs faq-item" style="top:2770px"><span style="font-size:26px;font-weight:700">+</span>What typs of insurance do you accept?</div>

<!-- news -->
<h2 class="abs news-title" style="left:667px;top:2490px">LATEST NEWS</h2>
<div class="abs news-photo" style="left:667px;top:2550px;height:112px" role="img" aria-label="Photo of a worried woman"></div>
<div class="abs news" style="left:798px;top:2550px;width:330px">
  <h4>Lorem Ipsum is simply dummy text</h4>
  <div class="date">&#9635; 10 JULY 2016</div>
  <p>Lorem Ipsum is simply dummy text of the printing and typesetting industry......</p>
  <div class="more">READ MORE &nbsp;&nbsp;&raquo;</div>
</div>
<div class="abs" style="left:798px;top:2682px;width:330px;height:1px;background:var(--line)"></div>
<div class="abs news-photo" style="left:667px;top:2710px;height:112px" role="img" aria-label="Photo of a child studying with a parent"></div>
<div class="abs news" style="left:798px;top:2710px;width:330px">
  <h4>Lorem Ipsum is simply dummy text</h4>
  <div class="date">&#9635; 10 JULY 2016</div>
  <p>Lorem Ipsum is simply dummy text of the printing and typesetting industry......</p>
  <div class="more">READ MORE &nbsp;&nbsp;&raquo;</div>
</div>

<!-- band -->
<div class="abs band"><p style="position:absolute;left:78px;top:26px;width:790px">Lorem Ipsum is simply dummy text of the printing and typesetting industry. Lorem Ipsum has been the industry's standard dummy text ever since the 1500s, when an unknown printer took a galley of type and scrambled.</p></div>
<div class="abs btn-white">NEW PATIENT FORM</div>

<!-- footer -->
<footer class="abs footer" role="img" aria-label="Darkened photo of smiling people as footer background"></footer>
<div class="abs foot-h" style="left:80px">QUICK INQUIRY</div>
<div class="abs field" style="top:3082px">Name*</div>
<div class="abs field" style="top:3132px">Email*</div>
<div class="abs field" style="top:3180px">Services*</div>
<div class="abs field" style="top:3226px;height:90px">Message*</div>
<div class="abs submit">SUBMIT</div>

<div class="abs foot-h" style="left:570px">OUR SERVICES</div>
<ul class="abs foot-list">
  <li>Home</li><li>About Us</li><li>Services</li><li>Conditions We Treat</li><li>New Patients</li><li>Contact Us</li>
</ul>

<div class="abs foot-h" style="left:873px">FIND US</div>
<svg class="abs" style="left:873px;top:3082px" width="18" height="24" viewBox="0 0 18 24"><path d="M9 0a9 9 0 0 1 9 9c0 7-9 15-9 15S0 16 0 9a9 9 0 0 1 9-9z" fill="var(--green)"/><circle cx="9" cy="9" r="3.5" fill="#2a1f1c"/></svg>
<div class="abs find" style="left:910px;top:3080px;width:230px">Maplecrest Behavioral Healthcare<br>Lorem Ipsum is simply dummy text printing and typesetting</div>
<svg class="abs" style="left:873px;top:3170px" width="20" height="20" viewBox="0 0 20 20"><path d="M3 1h4l2 5-3 2a11 11 0 0 0 6 6l2-3 5 2v4a2 2 0 0 1-2 2C8 19 1 12 1 3a2 2 0 0 1 2-2z" fill="var(--green)"/></svg>
<div class="abs find" style="left:910px;top:3170px">+1-555-010-2040</div>
<svg class="abs" style="left:873px;top:3215px" width="20" height="24" viewBox="0 0 20 24"><rect x="2" y="1" width="16" height="22" rx="2" fill="var(--green)"/><rect x="5" y="5" width="10" height="11" fill="#2a1f1c"/></svg>
<div class="abs find" style="left:910px;top:3218px">+1-555-010-2040</div>
<svg class="abs" style="left:873px;top:3262px" width="22" height="16" viewBox="0 0 22 16"><rect width="22" height="16" rx="2" fill="var(--green)"/><path d="M1 1l10 8 10-8" stroke="#2a1f1c" stroke-width="2" fill="none"/></svg>
<div class="abs find" style="left:910px;top:3260px">info@maplecresthealth.example</div>
<div class="abs social" style="left:875px"></div>
<div class="abs social" style="left:935px"></div>
<div class="abs social" style="left:995px"></div>

<div class="abs copyright">&copy; MAPLECREST BEHAVIORAL HEALTHCARE- 2017. All Rights Reserved</div>
</body>
</html>
```